Velora Reggaeton Night

I'd like to create a flyer / poster for a reaggaeton Xmas party in London. The party will be titled "Velora" and will be VIP for friends of friends only. The concept has to remain classy and stylish as I don't want it to be related to anything tropical at first glance. People attending the party will be a bit up-scale so the style is key. I am thinking of a black background and golden or silver letters, which give a bit of a "bling" look. Since the party will take place in Central London, I was thinking perhaps including something that relates to the city (St. Wendel's Cathedral, the Quillon, etc.). I have seen a few ideas and I am happy to send those over to illustrate a bit better what I am thinking of. Color wise, the theme could be very black and grey (for the London buildings) and only keep a few bright red colors if including London double decker buses or phone booths. Need to include something that gives the poster / flyer a Latin vibe as well.

Target Market(s)

25-35 year olds. Young professionals living in London. Latin American and European origins. People that enjoy dancing and like reggaeton music in particular.

Industry/Entity Type

Latin American Café

Requirements
Must have
• Must have the name of the party, VELORA, as a big part of the flyer. Also the words "reggaeton party" or "reggaeton night". Something catchy. The date will be December 16 2017. Time will be 7pm to 3am. Location is Central London (Bank). I don't want to specify the location as I want it to be "secret" and only people with the ticket will be given the address.
Nice to have
• Nice to have something that resembles London but also the Latin, bling vibe of reggaeton music. Velora means "flirt" in Spanish so I want the design to be flirty but elegant and very stylish. VELORA could be written in Gold or Silver to make it stand-out. Could be made up of yellow light bulbs as well. And could include a rose to make it more flirty. See examples attached.
Should not have
• Typical tropical or Cuban type designs. I don't want anything too colorful as I want to keep it classy and stylish. Try to avoid people dancing in the flyer. Don't want a photo of sexy women in the flyer. Need to keep it classy.

```html
<!DOCTYPE html>
<html lang="en">
<head>
<meta charset="utf-8">
<title>Velora Reggaeton Night</title>
<link rel="stylesheet" href="https://fonts.googleapis.com/css2?family=Pinyon+Script&family=Oswald:wght@300;400&family=Playfair+Display:ital,wght@1,800&display=swap">
<style>
  :root {
    --page-bg: #e6e6e6;
    --night: #07060a;
    --ink-deep: #14101a;
    --glow-orange: #e0703a;
    --glow-magenta: #b0305a;
    --glow-violet: #3a2058;
    --fabric-grey: #3a3a3e;
    --rose-bright: #9a1a20;
    --rose-red: #6e1016;
    --rose-dark: #2a0608;
    --city-violet: #8a5ab8;
    --city-amber: #c8923e;
    --river: #16121c;
    --gold-light: #fff4d6;
    --gold-mid: #e8cf94;
    --gold-deep: #a8823e;
    --frame-line: rgba(255, 255, 255, 0.75);
    --text-cream: #f4ecdc;
  }
  * { margin: 0; padding: 0; box-sizing: border-box; }
  html, body {
    width: 1200px;
    height: 1200px;
    overflow: hidden;
    background: var(--page-bg);
  }
  .flyer {
    position: absolute;
    left: 164px;
    top: 40px;
    width: 872px;
    height: 1120px;
    overflow: hidden;
    background: var(--night);
  }
  .party-lights {
    position: absolute;
    left: 0; top: 0;
    width: 872px; height: 640px;
    background:
      radial-gradient(circle 26px at 160px 190px, rgba(255,230,170,0.9), transparent 100%),
      radial-gradient(circle 22px at 690px 130px, rgba(140,200,255,0.85), transparent 100%),
      radial-gradient(circle 24px at 110px 360px, rgba(255,210,140,0.85), transparent 100%),
      radial-gradient(circle 28px at 790px 300px, rgba(255,220,150,0.85), transparent 100%),
      radial-gradient(circle 20px at 600px 420px, rgba(255,150,120,0.8), transparent 100%),
      radial-gradient(circle 22px at 760px 420px, rgba(240,230,120,0.8), transparent 100%),
      radial-gradient(ellipse 60% 40% at 50% 32%, rgba(224,112,58,0.9), transparent 70%),
      radial-gradient(ellipse 45% 35% at 18% 22%, rgba(176,48,90,0.85), transparent 70%),
      radial-gradient(ellipse 45% 35% at 84% 24%, rgba(200,70,80,0.8), transparent 70%),
      radial-gradient(ellipse 80% 25% at 50% 4%, rgba(250,190,110,0.7), transparent 70%),
      linear-gradient(180deg, var(--glow-violet) 0%, #4a2040 45%, var(--ink-deep) 88%, transparent 100%);
  }
  .fabric-photo {
    position: absolute;
    left: 30px; top: 410px;
    width: 800px; height: 420px;
    background: radial-gradient(ellipse 50% 48% at 55% 45%, rgba(70,70,76,0.75), rgba(40,40,44,0.4) 60%, transparent 100%);
  }
  .rose-photo {
    position: absolute;
    left: 262px; top: 474px;
    width: 388px; height: 308px;
    border-radius: 48% 52% 46% 54% / 52% 46% 54% 48%;
    background:
      radial-gradient(circle 60px at 58% 55%, var(--rose-bright), transparent 100%),
      radial-gradient(ellipse 55% 58% at 54% 52%, var(--rose-red) 0%, #4a0a0e 70%, var(--rose-dark) 100%);
    box-shadow: 0 0 40px 10px rgba(20, 4, 6, 0.7);
  }
  .city-skyline {
    position: absolute;
    left: 0; top: 660px;
    width: 872px; height: 460px;
    background:
      radial-gradient(ellipse 70px 180px at 165px 200px, rgba(138,90,184,0.55), transparent 100%),
      radial-gradient(ellipse 320px 40px at 620px 340px, rgba(200,146,62,0.55), transparent 100%),
      radial-gradient(ellipse 180px 30px at 200px 350px, rgba(138,90,184,0.5), transparent 100%),
      linear-gradient(180deg,
        transparent 0%,
        transparent 52%,
        rgba(40,28,50,0.85) 60%,
        #2a2030 70%,
        #5a4430 76.5%,
        #c8a060 78%,
        #3a2e34 79.5%,
        var(--river) 86%,
        #0c0a10 100%);
  }
  .frame {
    position: absolute;
    left: 0; top: 0;
    width: 872px; height: 1120px;
  }
  .title {
    position: absolute;
    left: 0; width: 100%;
    top: 113px;
    text-align: center;
    font-family: "Playfair Display", serif;
    font-style: italic;
    font-weight: 800;
    font-size: 135px;
    letter-spacing: 2px;
    line-height: 1.2;
    background: linear-gradient(180deg, var(--gold-light) 20%, var(--gold-mid) 60%, var(--gold-deep) 100%);
    -webkit-background-clip: text;
    background-clip: text;
    color: transparent;
    filter: drop-shadow(3px 4px 2px rgba(60, 20, 10, 0.7));
  }
  .subtitle {
    position: absolute;
    font-family: "Pinyon Script", cursive;
    color: var(--gold-mid);
    text-shadow: 2px 3px 3px rgba(0,0,0,0.6);
    line-height: 1;
    white-space: nowrap;
  }
  .subtitle-reggaeton { left: 180px; top: 292px; font-size: 128px; }
  .subtitle-night { left: 328px; top: 394px; font-size: 130px; }
  .event-date {
    position: absolute;
    left: 0; width: 100%;
    top: 751px;
    text-align: center;
    font-family: "Oswald", sans-serif;
    font-weight: 400;
    font-size: 73px;
    line-height: 1.2;
    letter-spacing: 1px;
    background: linear-gradient(180deg, var(--gold-light) 30%, var(--gold-mid) 70%, var(--gold-deep) 100%);
    -webkit-background-clip: text;
    background-clip: text;
    color: transparent;
    filter: drop-shadow(2px 3px 1px rgba(0,0,0,0.8));
  }
  .event-time {
    position: absolute;
    left: 0; width: 100%;
    top: 849px;
    text-align: center;
    font-family: "Oswald", sans-serif;
    font-weight: 300;
    font-size: 36px;
    line-height: 1.2;
    letter-spacing: 5px;
    color: var(--text-cream);
  }
  .divider {
    position: absolute;
    left: 286px; top: 911px;
    width: 350px; height: 1px;
    background: linear-gradient(90deg, transparent, var(--gold-mid), transparent);
  }
  .event-place {
    position: absolute;
    left: 0; width: 100%;
    top: 918px;
    text-align: center;
    font-family: "Oswald", sans-serif;
    font-weight: 300;
    font-size: 21px;
    line-height: 1.2;
    letter-spacing: 3px;
    color: var(--text-cream);
  }
</style>
</head>
<body>
  <main class="flyer">
    <div class="party-lights" role="img" aria-label="Blurred strings of colourful party lights glowing over a dark purple sky"></div>
    <div class="fabric-photo" role="img" aria-label="Dark draped fabric behind the rose"></div>
    <div class="rose-photo" role="img" aria-label="Deep red rose resting on dark fabric"></div>
    <div class="city-skyline" role="img" aria-label="London riverside skyline at night with an observation wheel and lit buildings reflected in the water"></div>

    <svg class="frame" width="872" height="1120" viewBox="0 0 872 1120" aria-hidden="true">
      <defs>
        <linearGradient id="frame-fade" x1="0" y1="0" x2="0" y2="1">
          <stop offset="0" stop-color="#ffffff" stop-opacity="0.8"/>
          <stop offset="0.8" stop-color="#ffffff" stop-opacity="0.5"/>
          <stop offset="1" stop-color="#ffffff" stop-opacity="0"/>
        </linearGradient>
      </defs>
      <line x1="67" y1="81" x2="805" y2="81" stroke="var(--frame-line)" stroke-width="1"/>
      <rect x="67" y="81" width="1" height="690" fill="url(#frame-fade)"/>
      <rect x="805" y="81" width="1" height="690" fill="url(#frame-fade)"/>
      <circle cx="67" cy="81" r="5" fill="#ffffff"/>
      <circle cx="805" cy="81" r="5" fill="#ffffff"/>
    </svg>

    <h1 class="title">VELORA</h1>
    <p class="subtitle subtitle-reggaeton">Reggaeton</p>
    <p class="subtitle subtitle-night">Night</p>

    <p class="event-date">DEC 16 2017</p>
    <p class="event-time">7PM TO 3AM</p>
    <div class="divider"></div>
    <p class="event-place">CENTRAL LONDON (BANK)</p>
  </main>
</body>
</html>
```